Tarlow Plumbing & Heating Limited needs a service and maintenance contract document design

Tarlow Plumbing & Heating Limited are a well established family owned and operated company.

We currently offer installation, service and repair services for gas, plumbing, heating and electrical work. We wish to offer service and maintenance plans for plumbing, heating and electrical for our domestic clients in the UK. We would like the brochure to incorporate our company logo and colours, and reflect the reliable, quality, 5 star service we offer our clients.
I have attached a brochure that a friends company uses to give a good idea of the structure of the plans we wish to offer. We want to give our customers a choice in what packages best suit their needs. However, the pricing structure and certain elements/content of what we offer will be slightly different due to our geographical location.

We would like to have the basic structure of the brochure put in place and the
text content editable to our specific needs. Looking for advice on this but we do have Acrobat DC if we need to edit the text ourselves?

We use our logo with "TARLOW" in white over a grey backgound.

Our website is - www.tarlow.plumbing
Facebook and twitter handle is - @TarlowHeating

Target Market(s)

UK domestic plumbing, heating, natural gas, LPG and electrical market. Both private homeowners and landlords. Please see both the domestic and landlord document files attached for an idea on what we'd like.

Colors

Designer to choose colors to be used in the design.

Requirements
Must have
• Would like the finished design to incorporate the branding and colours we already use. Professional, Contemporary designs that will stand out above our competition.
• The content of the brochures MUST be very similar in structure to the files I’ve attached to the brief.
• We are having many designs submitted that are just copying our website content. This is not what we are asking for.
• I would like the icons etc to be redesigned so they are ours and not copied.
• Please also see the Landlords brochure attached to the brief. We would like this to be a separate document but to reflect the same design as the homeowner design you submit.
• The content of the documents will need to be re worded for our own use but I'm happy to change this once the design element is in place.
• A4 sized pages as per the example I've attached
• Must be able to attach the document to our website for clients to download.
Nice to have
• A4 sized pages as per the examples I've attached
Should not have
• Please DO NOT copy the content from our website to create our service plan brochures. This is not what we are after. As above, we need the brochures to be like the ones we've provided but made to fit our brand.
• Thank you

```html
<!DOCTYPE html>
<html lang="en">
<head>
<meta charset="utf-8">
<title>Tarlow Plumbing &amp; Heating – Service Plans, Pages 8–9</title>
<link href="https://fonts.googleapis.com/css2?family=Roboto+Condensed:wght@300;400;700&family=Oswald:wght@400;500&family=Caveat:wght@400&display=swap" rel="stylesheet">
<style>
  :root{
    --backdrop:#3f3f41;
    --paper:#ffffff;
    --paper-shade:#e4e4e6;
    --orange:#f7941d;
    --orange-deep:#f15a24;
    --blue:#29a8e0;
    --blue-deep:#1a7cc1;
    --ink:#3a3a3a;
    --ink-soft:#555;
    --rule:#8a8a8a;
  }
  *{box-sizing:border-box;margin:0;padding:0}
  html,body{width:1200px;height:884px;overflow:hidden;background:var(--backdrop)}
  body{position:relative;font-family:"Roboto Condensed",Arial,sans-serif;color:var(--ink)}

  .page{position:absolute;top:78px;width:516px;height:728px;overflow:hidden;
    background:linear-gradient(90deg,var(--paper-shade) 0,var(--paper) 16%,var(--paper) 100%)}
  .page--left{left:80px}
  .page--right{left:604px}

  .page__rule{position:absolute;left:24px;width:468px;height:1px;background:var(--rule)}
  .page__rule--top{top:66px}
  .page__rule--bottom{top:686px}

  .brand{position:absolute;left:330px;top:24px;display:flex;align-items:center;gap:8px}
  .brand__dot{width:30px;height:30px;border-radius:50%;background:var(--blue-deep)}
  .brand__name{font-weight:700;font-size:28px;letter-spacing:1px;color:#2d2d2d;line-height:1}

  .tagline{position:absolute;left:26px;top:42px;font-family:"Caveat",cursive;font-size:22px;color:#444}

  .plan-panel{position:absolute;left:0;top:86px;width:508px;border-radius:0 20px 20px 0;
    background:linear-gradient(180deg,var(--orange) 0%,#f7881f 55%,var(--orange-deep) 100%)}
  .page--left .plan-panel{height:310px}
  .page--right .plan-panel{height:318px}

  .plan-panel__title{position:absolute;left:25px;top:22px;font-family:"Oswald",sans-serif;font-weight:500;font-size:14px;color:#fff;letter-spacing:.2px}
  .page--right .plan-panel__title{left:24px;top:12px}
  .plan-panel__body{position:absolute;left:25px;top:44px;width:312px;font-weight:300;font-size:9.4px;line-height:12px;color:#fff}
  .page--right .plan-panel__body{left:24px;top:33px;width:344px}
  .plan-panel__body p+p{margin-top:11px}

  .price-card{position:absolute;left:372px;top:14px;width:120px;height:117px;border-radius:20px;background:#fff;
    display:flex;align-items:center;justify-content:center}
  .page--right .price-card{left:374px;top:14px;height:115px}

  .cover-table{position:absolute;left:16px;width:486px;background:#fff;border-radius:14px;overflow:hidden;font-size:8.2px;font-weight:300;color:var(--ink-soft)}
  .page--left .cover-table{top:135px;height:168px}
  .page--right .cover-table{left:14px;top:154px;height:156px}
  .cover-table__head{height:28px;padding:11px 0 0 24px;font-size:9.6px;font-weight:400;color:#333;border-bottom:1px solid #555}
  .page--right .cover-table__head{height:23px;padding:8px 0 0 24px}
  .cover-table__cols{display:flex;border-bottom:1px solid #555}
  .page--left .cover-table__cols{height:116px}
  .page--right .cover-table__cols{height:109px}
  .cover-table__col{padding:6px 8px 0 24px}
  .cover-table__col--in{width:218px;border-right:1px solid #555}
  .cover-table__col--out{flex:1;padding-left:8px}
  .cover-table__label{font-size:9.6px;font-weight:400;color:var(--orange-deep);margin-bottom:8px}
  .page--right .cover-table__label{font-size:7.6px;font-weight:300;color:var(--ink-soft);margin-bottom:12px}
  .page--right .cover-table__col{padding-top:10px}
  .cover-table__col p{font-size:6.8px;line-height:9px;margin-bottom:4px}
  .bullets{display:grid;grid-template-columns:72px 1fr;column-gap:4px;font-size:6.8px;line-height:9px;list-style:none;margin-top:10px}
  .page--right .bullets{grid-template-columns:84px 1fr;row-gap:3px;margin-top:4px}
  .bullets li::before{content:"• "}
  .cover-table__note{font-size:5.6px;text-align:center;padding-top:6px;color:#555}

  .photo{position:absolute}
  .photo--family{left:11px;top:452px;width:179px;height:225px;border-radius:0 0 12px 0;
    background:linear-gradient(135deg,#d8c7b4 0%,#b7a38e 40%,#8c98a6 70%,#dcdcdc 100%)}
  .photo--lounge{left:202px;top:452px;width:314px;height:225px;border-radius:12px 0 0 12px;
    background:linear-gradient(100deg,#6b5444 0%,#3b2c24 35%,#4a3a30 60%,#b0a59b 100%)}

  .pack-title{position:absolute;right:38px;font-family:"Oswald",sans-serif;font-weight:400;font-size:13.4px;color:#2d2d2d;white-space:nowrap}
  .pack-title b{font-size:18px;font-weight:500}
  .pack-title--twin{top:452px}
  .pack-title--triple{top:561px}
  .pack-badges{position:absolute;display:flex;gap:2px}
  .pack-badges--twin{left:352px;top:482px}
  .pack-badges--triple{left:300px;top:592px}

  .savings__head{position:absolute;left:30px;top:462px;font-family:"Oswald",sans-serif;font-size:31px;line-height:42px;color:var(--orange-deep);font-weight:400}
  .savings__body{position:absolute;left:30px;top:600px;width:126px;font-size:8.2px;line-height:11.3px;color:#333;font-weight:300}

  .folio{position:absolute;top:696px;font-weight:700;font-size:10px;color:#333}
  .page--left .folio{right:24px}
  .page--right .folio{left:30px}

  .plan-badge text{font-family:"Roboto Condensed",sans-serif;fill:#fff}
</style>
</head>
<body>

<svg width="0" height="0" style="position:absolute" aria-hidden="true">
  <defs>
    <linearGradient id="badgeTop" x1="0" y1="0" x2="0" y2="1">
      <stop offset="0" stop-color="#f7941d"/><stop offset="1" stop-color="#f15a24"/>
    </linearGradient>
    <linearGradient id="badgeFoot" x1="0" y1="0" x2="1" y2="0">
      <stop offset="0" stop-color="#1a7cc1"/><stop offset="1" stop-color="#29a8e0"/>
    </linearGradient>
    <clipPath id="badgeClip"><rect x="4" y="4" width="92" height="102" rx="18"/></clipPath>
    <symbol id="badgeBase" viewBox="0 0 100 110">
      <g clip-path="url(#badgeClip)">
        <rect width="100" height="58" fill="url(#badgeTop)"/>
        <rect y="58" width="100" height="52" fill="url(#badgeFoot)"/>
        <rect y="57" width="100" height="2.5" fill="#fff"/>
      </g>
    </symbol>
    <symbol id="iconBoiler" viewBox="0 0 20 24"><rect x="2" y="1" width="16" height="20" rx="1" fill="none" stroke="#fff" stroke-width="1.6"/><rect x="6" y="14" width="8" height="3" fill="none" stroke="#fff" stroke-width="1.2"/></symbol>
    <symbol id="iconGauge" viewBox="0 0 24 24"><circle cx="12" cy="12" r="9" fill="none" stroke="#fff" stroke-width="1.6"/><path d="M12 13L17 8" stroke="#fff" stroke-width="1.6"/></symbol>
    <symbol id="iconRadiator" viewBox="0 0 24 20"><rect x="1" y="2" width="22" height="15" fill="none" stroke="#fff" stroke-width="1.4"/><path d="M5 2v15M9 2v15M13 2v15M17 2v15" stroke="#fff" stroke-width="1.4"/></symbol>
  </defs>
</svg>

<!-- Page 9 -->
<section class="page page--left">
  <div class="brand"><span class="brand__dot"></span><span class="brand__name">TARLOW</span></div>
  <div class="page__rule page__rule--top"></div>

  <div class="plan-panel">
    <h2 class="plan-panel__title">Central Heating Maintenance</h2>
    <div class="plan-panel__body">
      <p>Our Central Heating maintenance plan covers your radiators and associated systems listed below, keeping them in good working order so you and your family can stay nice and toasty during colder weather. No one wants to feel cold in the winter, but we'd especially recommend this plan if your household includes children, vulnerable adults or older people.</p>
    </div>
    <div class="price-card">
      <svg class="plan-badge" width="96" height="104" viewBox="0 0 100 110">
        <use href="#badgeBase"/>
        <text x="50" y="44" text-anchor="middle" font-size="30" font-weight="700">£6</text>
        <use href="#iconBoiler" x="18" y="71" width="18" height="22"/>
        <text x="42" y="86" font-size="11">Boiler</text>
      </svg>
    </div>

    <div class="cover-table">
      <div class="cover-table__head">What is and isn't included in our Central Heating Maintenance plan</div>
      <div class="cover-table__cols">
        <div class="cover-table__col cover-table__col--in">
          <div class="cover-table__label">Included</div>
          <p>Repairing or replacing:</p>
          <ul class="bullets">
            <li>Radiators<br>• Radiator valves</li>
            <li>All water pipes linking your boiler with your radiators and expansion tank.</li>
          </ul>
        </div>
        <div class="cover-table__col cover-table__col--out">
          <div class="cover-table__label" style="margin-bottom:3px">Excluded</div>
          <p>Warm air and underfloor central heating systems.</p>
        </div>
      </div>
      <p class="cover-table__note">Please also read our General Exclusions and Limitations on page 17 to find out what's not covered under any of our plans, or where the cover we provide is limited.</p>
    </div>
  </div>

  <div class="photo photo--family" role="img" aria-label="Photo of a smiling couple relaxing at home with a tablet"></div>

  <h3 class="pack-title pack-title--twin">Heating Twin Pack <b>£5</b></h3>
  <div class="pack-badges pack-badges--twin">
    <svg class="plan-badge" width="58" height="64" viewBox="0 0 100 110"><use href="#badgeBase"/><use href="#iconGauge" x="14" y="72" width="20" height="20"/><text x="40" y="87" font-size="11">Controls</text></svg>
    <svg class="plan-badge" width="58" height="64" viewBox="0 0 100 110"><use href="#badgeBase"/><use href="#iconRadiator" x="12" y="73" width="22" height="18"/><text x="40" y="80" font-size="10">Central</text><text x="40" y="93" font-size="10">heating</text></svg>
  </div>

  <h3 class="pack-title pack-title--triple">Heating Triple Pack <b>£10</b></h3>
  <div class="pack-badges pack-badges--triple">
    <svg class="plan-badge" width="58" height="64" viewBox="0 0 100 110"><use href="#badgeBase"/><use href="#iconBoiler" x="16" y="71" width="18" height="22"/><text x="42" y="87" font-size="11">Boiler</text></svg>
    <svg class="plan-badge" width="58" height="64" viewBox="0 0 100 110"><use href="#badgeBase"/><use href="#iconGauge" x="14" y="72" width="20" height="20"/><text x="40" y="87" font-size="11">Controls</text></svg>
    <svg class="plan-badge" width="58" height="64" viewBox="0 0 100 110"><use href="#badgeBase"/><use href="#iconRadiator" x="12" y="73" width="22" height="18"/><text x="40" y="80" font-size="10">Central</text><text x="40" y="93" font-size="10">heating</text></svg>
  </div>

  <div class="page__rule page__rule--bottom"></div>
  <div class="folio">Page 9</div>
</section>

<!-- Page 8 -->
<section class="page page--right">
  <div class="tagline">We care</div>
  <div class="brand"><span class="brand__dot"></span><span class="brand__name">TARLOW</span></div>
  <div class="page__rule page__rule--top"></div>

  <div class="plan-panel">
    <h2 class="plan-panel__title">Boiler Service</h2>
    <div class="plan-panel__body">
      <p>We've designed our Controls Maintenance plan to cover the cost of repairing or replacing the electrical equipment that controls how your heating and hot water systems work. To give an example, if your circulating central heating pump breaks down, then you'll still have no central heating even if there are no problems with your boiler, pipes or radiators.</p>
      <p>Having our Controls Maintenance plan gives you the extra peace of mind that, if a fault develops with your control system that stops your central heating or hot water system from working, the cost of repair or replacement will be covered.</p>
    </div>
    <div class="price-card">
      <svg class="plan-badge" width="96" height="104" viewBox="0 0 100 110">
        <use href="#badgeBase"/>
        <text x="50" y="44" text-anchor="middle" font-size="30" font-weight="700">£3</text>
        <use href="#iconGauge" x="14" y="72" width="20" height="20"/>
        <text x="40" y="87" font-size="11">Controls</text>
      </svg>
    </div>

    <div class="cover-table">
      <div class="cover-table__head">What is and isn't included in our Controls Maintenance plan</div>
      <div class="cover-table__cols">
        <div class="cover-table__col cover-table__col--in">
          <div class="cover-table__label">Included</div>
          <p>Repairing or replacing any electrical components of your hot water or central heating system which are connected to, but not located inside, your boiler.</p>
          <p>These might include your:</p>
          <ul class="bullets">
            <li>Programmer</li><li>Circulating central heating pumps</li>
            <li>Motorised zone valves</li><li>Circulating hot water pumps</li>
            <li>Cylinder thermostat</li><li>Room and frost thermostats</li>
          </ul>
        </div>
        <div class="cover-table__col cover-table__col--out">
          <div class="cover-table__label" style="margin-bottom:8px">Excluded</div>
          <p>Any electrical components of your hot water or central heating system located inside your boiler. These would be covered by our Boiler Maintenance plan.</p>
          <p style="margin-top:10px">Any pumps not listed opposite.</p>
        </div>
      </div>
      <p class="cover-table__note">Please also read our General Exclusions and Limitations on page 17 to find out what's not covered under any of our plans, or where the cover we provide is limited.</p>
    </div>
  </div>

  <h2 class="savings__head">Save money<br>by adding our<br>plans together</h2>
  <p class="savings__body">You can reduce the costs of some of our individual plans by adding them together, as shown opposite. This gives you all the benefits of enhanced protection for a lower price than buying the plans separately.</p>

  <div class="photo photo--lounge" role="img" aria-label="Photo of a man relaxing on a leather sofa with a tablet in front of bookshelves"></div>

  <div class="page__rule page__rule--bottom"></div>
  <div class="folio">Page 8</div>
</section>

</body>
</html>
```